Website Design for Kids

We need to redesign our site pobtrundle.net.
Current site was done long ago in Flash. We need to remove Flash and create a responsive site which can be viewed on phone, tablets as well as PC.
We are looking for a new fresh design. No elements from existing design need to be incorporated into new design.
The site is targeted for kids 7-12 years old.
Design should have attractive colors and it should be easy to navigate. It will be even better to provide one theme for boys and one for girls.
New site will have following features:
SHORT STORIES
Ability to display thumbnails of stories available. When user click a story it will play.
See http://pobtrundle.net/stories/index.asp to get an idea.
MOVIES
We have two moves, more to come. Users will be able to see thumbnails and watch trailers. To watch full movie they will be redirect to a Plonta page where they can pay and watch.
See http://pobtrundle.net/Movies/ to get an idea.
PICTURE STORIES
This will feature short stories. When a story is clicked it will start playing. The stories will have picture and text, possibly audio too.
See http://pobtrundle.net/stories/stories.asp to get an idea.
AUDIO STORIES
Audio stories recorded from kids or adults will be played. Optional photo of the person who recorded story will be displayed. User will have option to select a story by clicking thumbnail of stories.
VIDEO STORIES
Like audio stories, user will be able to scroll though thumbnails of stories and play one. Short video 1-3 mins will be played.
- I have upgraded budget and added a few more simple requirements. Need to decide soon so please submit your designs asap.
Number of Pages Required
5+ page
Look and feel

```html
<!DOCTYPE html>
<html lang="en">
<head>
<meta charset="utf-8">
<title>Pobtrundle – Stories, Movies and Fun for Kids</title>
<link href="https://fonts.googleapis.com/css2?family=Fredoka:wght@500;600&family=Oswald:wght@600&family=Overlock:wght@700&family=Open+Sans:wght@400;600&family=Arimo&display=swap" rel="stylesheet">
<style>
:root{
  --purple:#8a55d6; --sky:#3fb1d8; --teal:#3bbd9c; --lime:#8cc21f; --amber:#f6a01a; --red:#f0432f; --pink:#d3287b;
  --green-card:#88b21c; --orange-card:#fb8a0c; --blue-card:#2f49a8;
  --btn-green:#6e9318; --btn-orange:#e37a09;
  --ink:#555; --heading:#5a5a5a; --muted:#777; --footer:#333; --accent:#e4521f;
}
*{margin:0;padding:0;box-sizing:border-box}
html,body{width:956px;height:1200px;overflow:hidden;background:#fff}
body{position:relative;font-family:"Arimo",Arial,sans-serif;color:var(--ink)}
.top-stripe{position:absolute;top:0;left:0;width:956px;height:2px;
  background:linear-gradient(90deg,var(--amber) 0 19%,#1d4fa0 19% 41%,#f4b615 41% 63%,#5ec4ea 63% 84%,#2d9a2c 84%)}
.brand{position:absolute;top:30px;left:0;width:956px;text-align:center;
  font-family:"Fredoka",sans-serif;font-weight:600;font-size:30px;color:#4b3fc4}
.brand::before{content:"";display:inline-block;width:14px;height:14px;border-radius:50%;background:#4b3fc4;margin-right:8px;vertical-align:middle}
.main-nav{position:absolute;left:78px;top:114px;display:flex;width:800px}
.main-nav a{flex:1;height:38px;line-height:38px;text-align:center;color:#fff;text-decoration:none;
  font-family:"Fredoka",sans-serif;font-weight:600;font-size:18px;margin-right:1px;box-shadow:inset 0 -3px 0 rgba(0,0,0,.12)}
.main-nav a:last-child{margin-right:0}
.main-nav .home{background:var(--purple);margin-top:-4px;height:42px;line-height:40px}
.main-nav .games{background:var(--sky)} .main-nav .stories{background:var(--teal)}
.main-nav .movies{background:var(--lime)} .main-nav .activities{background:var(--amber)}
.main-nav .fun{background:var(--red)} .main-nav .shop{background:var(--pink)}
.hero{position:absolute;left:78px;top:157px;width:800px;height:350px}
.hero-shadow{position:absolute;left:165px;top:490px;width:630px;height:18px;border-radius:50%;
  background:radial-gradient(ellipse at center,rgba(0,0,0,.45),rgba(0,0,0,0) 70%)}
.feature{position:absolute;top:550px;width:239px;height:295px;border-radius:3px;color:#fff;padding:10px;
  box-shadow:0 8px 10px -6px rgba(0,0,0,.35);overflow:hidden}
.feature h2{font-family:"Oswald",sans-serif;font-weight:600;font-size:24px;line-height:28px;margin:4px 0 9px 0;letter-spacing:.2px}
.feature .thumb{height:135px;border:2px solid #fff;border-radius:3px}
.feature p{font-size:8px;line-height:15.5px;margin:12px 2px 0 3px}
.feature .more{display:inline-block;margin:9px 0 0 3px;padding:0 10px;height:25px;line-height:25px;font-family:"Open Sans",sans-serif;font-size:10.5px;color:#fff;text-decoration:none}
.feature .bubble{position:absolute;border-radius:50%;background:rgba(255,255,255,.1)}
.short{left:88px;background:var(--green-card)} .short .more{background:var(--btn-green)}
.movies-card{left:358px;background:var(--orange-card)} .movies-card .more{background:var(--btn-orange)}
.picture{left:630px;background:var(--blue-card)} .picture .more{background:var(--btn-green)}
.block-title{position:absolute;top:896px;font-family:"Overlock",sans-serif;font-weight:700;font-size:18px;color:var(--heading)}
.quick{position:absolute;left:78px;top:932px;width:250px}
.quick p{font-size:8px;line-height:15px;color:var(--muted)}
.quick ul{list-style:none;margin-top:12px}
.quick li{font-family:"Open Sans",sans-serif;font-size:9.5px;line-height:20.5px;color:#555;display:flex;align-items:center}
.quick li svg{margin-right:10px}
.welcome-art{position:absolute;left:353px;top:926px;width:246px;height:116px;border:3px solid #e4e4e4}
.welcome-text{position:absolute;left:355px;top:1055px;width:246px;font-size:8px;line-height:15.5px;color:var(--muted)}
.welcome-text a{color:var(--accent);text-decoration:none}
.newsletter{position:absolute;left:640px;top:926px;width:237px;height:158px;border:1px solid #e6e6e6;padding:12px}
.newsletter label{display:block;width:211px;height:24px;border:1px solid #ddd;margin-bottom:7px;font-size:8.5px;line-height:22px;padding-left:6px;color:#888}
.newsletter .apply{display:inline-block;margin-top:9px;padding:0 10px;height:26px;line-height:26px;background:var(--btn-orange);color:#fff;font-family:"Open Sans",sans-serif;font-weight:600;font-size:11px}
.site-footer{position:absolute;left:0;top:1124px;width:956px;height:76px;background:var(--footer)}
.site-footer small{position:absolute;left:78px;top:33px;color:#fff;font-size:8px}
.social{position:absolute;left:752px;top:26px;display:flex;gap:3px}
.social span{width:29px;height:29px;border-radius:50%;border:2px solid #ddd}
</style>
</head>
<body>
<div class="top-stripe"></div>
<div class="brand">Pobtrundle</div>

<nav class="main-nav">
  <a class="home" href="#">Home</a><a class="games" href="#">Games</a><a class="stories" href="#">Stories</a>
  <a class="movies" href="#">Movies</a><a class="activities" href="#">Activities</a><a class="fun" href="#">Fun Stuff</a><a class="shop" href="#">Shop</a>
</nav>

<div class="hero-shadow"></div>
<svg class="hero" viewBox="0 0 800 350" role="img" aria-label="Slideshow illustration: a storyteller with a wheelbarrow meets two travellers under a golden parasol in a desert village">
  <defs>
    <linearGradient id="heroFill" x1="0" y1="0" x2="0" y2="1">
      <stop offset="0" stop-color="#b7d6e6"/><stop offset=".45" stop-color="#a49a8e"/><stop offset=".7" stop-color="#8fc24a"/><stop offset="1" stop-color="#e9b98c"/>
    </linearGradient>
  </defs>
  <path d="M1 1H799V320Q400 390 1 320Z" fill="url(#heroFill)" stroke="#e6e6e6" stroke-width="2"/>
  <circle cx="380" cy="327" r="4" fill="#c8102e"/><circle cx="393" cy="327" r="4" fill="#fff"/>
  <circle cx="407" cy="327" r="4" fill="#c8102e"/><circle cx="420" cy="327" r="4" fill="#c8102e"/>
</svg>

<section class="feature short">
  <span class="bubble" style="width:90px;height:90px;left:190px;top:-30px"></span>
  <h2>SHORT STORIES</h2>
  <div class="thumb" role="img" aria-label="Illustration: a boy sitting on a bench beside a framed landscape painting" style="background:linear-gradient(160deg,#f6d76a,#e8b04a 60%,#c9a27a)"></div>
  <p>It is a long established fact that a reader will be distracted by the readable content of a page when looking at its Ipsum is that it has a more-or-less</p>
  <a class="more" href="http://pobtrundle.net/stories/index.asp">READ MORE</a>
</section>

<section class="feature movies-card">
  <h2>MOVIES</h2>
  <div class="thumb" role="img" aria-label="Illustration: an old woman and a man in a headscarf before a village at sunset" style="background:linear-gradient(180deg,#e8562a,#f3a03a 55%,#d9a765)"></div>
  <p>It is a long established fact that a reader will be distracted by the readable content of a page when looking at its Ipsum is that it has a more-or-less</p>
  <a class="more" href="http://pobtrundle.net/Movies/">READ MORE</a>
</section>

<section class="feature picture">
  <span class="bubble" style="width:70px;height:70px;left:150px;top:-20px"></span>
  <span class="bubble" style="width:50px;height:50px;left:215px;top:190px"></span>
  <h2>PICTURE STORIES</h2>
  <div class="thumb" role="img" aria-label="Illustration: a king in a turban and a guard in front of a domed palace" style="background:linear-gradient(180deg,#4fc6e4,#a7dff0 45%,#d08a2a)"></div>
  <p>It is a long established fact that a reader will be distracted by the readable content of a page when looking at its Ipsum is that it has a more-or-less</p>
  <a class="more" href="http://pobtrundle.net/stories/stories.asp">READ MORE</a>
</section>

<h3 class="block-title" style="left:78px">Visit These Quick Links</h3>
<div class="quick">
  <p>It is a long established fact that a reader will be distracted by the readable content of a page when looking at its layout. The point of or-less normal letters, like readable English.....</p>
  <ul>
    <li><svg width="8" height="8" viewBox="0 0 8 8"><circle cx="4" cy="4" r="3.3" fill="none" stroke="#e4521f" stroke-width="1.2"/><path d="M3.2 2.6 4.7 4 3.2 5.4" fill="none" stroke="#e4521f" stroke-width="1.1"/></svg>Play Puzzle Fun</li>
    <li><svg width="8" height="8" viewBox="0 0 8 8"><circle cx="4" cy="4" r="3.3" fill="none" stroke="#e4521f" stroke-width="1.2"/><path d="M3.2 2.6 4.7 4 3.2 5.4" fill="none" stroke="#e4521f" stroke-width="1.1"/></svg>Send An E-Card</li>
    <li><svg width="8" height="8" viewBox="0 0 8 8"><circle cx="4" cy="4" r="3.3" fill="none" stroke="#e4521f" stroke-width="1.2"/><path d="M3.2 2.6 4.7 4 3.2 5.4" fill="none" stroke="#e4521f" stroke-width="1.1"/></svg>Watch The Ark</li>
    <li><svg width="8" height="8" viewBox="0 0 8 8"><circle cx="4" cy="4" r="3.3" fill="none" stroke="#e4521f" stroke-width="1.2"/><path d="M3.2 2.6 4.7 4 3.2 5.4" fill="none" stroke="#e4521f" stroke-width="1.1"/></svg>Click N Colour</li>
    <li><svg width="8" height="8" viewBox="0 0 8 8"><circle cx="4" cy="4" r="3.3" fill="none" stroke="#e4521f" stroke-width="1.2"/><path d="M3.2 2.6 4.7 4 3.2 5.4" fill="none" stroke="#e4521f" stroke-width="1.1"/></svg>Word Search</li>
  </ul>
</div>

<h3 class="block-title" style="left:353px">Welcome TO Our Site</h3>
<div class="welcome-art" role="img" aria-label="Illustration: two elderly men talking in a fruit orchard" style="background:linear-gradient(180deg,#5aa83a,#7dbb45 60%,#b98a55)"></div>
<p class="welcome-text">It is a long established fact that a reader will be distracted by the readable content of a page when looking at its layout. The point of or-less normal letters, like readable English.....<a href="#">RAED MORE</a></p>

<h3 class="block-title" style="left:638px">NewsLetter</h3>
<form class="newsletter">
  <label>Name :</label><label>Email :</label><label>Phone :</label>
  <span class="apply">APPLY NOW</span>
</form>

<footer class="site-footer">
  <small>© Copy Right 2105 Pobtrundle .All copyrights Reserved.</small>
  <div class="social"><span></span><span></span><span></span><span></span></div>
</footer>
</body>
</html>
```